Business Card for Vorla Parts Wholesale supplier

Hi There! I need a new business card for our company. We are specialized in selling Vorla parts, mostly we sell new LCD screens for Zelnar and Drelks. I would like to see that back in the design.

You can find the colors and logo's on our website: www.hartuvo.nl

Industry/Entity Type

Business

Contact Information for Business Card

My Details:
Tobias Lindqvist

Phone: 0031687203316
E-mail: Tobias@hartuvo.nl

Slogan: "Because Quality Matters"

Font styles to use
Sans Serif

Colors

Designer to choose colors to be used in the design.

Requirements
Must have
• A Black backside with the Hartuvo logo on it. The front side should be clean with only my contact details.
• But I'm also open for something really different or awesome!
Nice to have
• Remember that we are in the parts & repairing industry, So i'll be handing those business cards mainly to repair companies. Maybe you can do something with that thought :)

```html
<!DOCTYPE html>
<html lang="en">
<head>
<meta charset="utf-8">
<title>Hartuvo Business Card</title>
<link href="https://fonts.googleapis.com/css2?family=Open+Sans:wght@400;700&display=swap" rel="stylesheet">
<style>
  :root {
    --stage: #2f2a27;
    --ink: #111111;
    --paper: #ffffff;
    --card-black: #050505;
    --accent: #f26a21;
    --text: #1a1a1a;
  }
  * { margin: 0; padding: 0; box-sizing: border-box; }
  html, body { width: 1200px; height: 780px; overflow: hidden; }
  body {
    background: var(--stage);
    font-family: "Open Sans", Arial, sans-serif;
    display: flex;
    align-items: center;
    justify-content: center;
    gap: 50px;
  }
  .card {
    width: 520px;
    height: 320px;
    position: relative;
    box-shadow: 0 10px 30px rgba(0,0,0,0.45);
  }
  .card--back {
    background: var(--card-black);
    display: flex;
    align-items: center;
    justify-content: center;
  }
  .card--front { background: var(--paper); }

  .brand {
    display: flex;
    align-items: center;
    gap: 14px;
  }
  .brand__mark {
    width: 44px;
    height: 44px;
    background: var(--accent);
  }
  .brand__name {
    font-weight: 700;
    font-size: 58px;
    letter-spacing: 1px;
    line-height: 1;
  }
  .card--back .brand__name { color: var(--paper); }
  .card--front .brand {
    position: absolute;
    top: 40px;
    left: 40px;
  }
  .card--front .brand__mark { width: 38px; height: 38px; }
  .card--front .brand__name { color: var(--ink); font-size: 50px; }

  .contact {
    position: absolute;
    left: 40px;
    top: 158px;
    color: var(--text);
    font-size: 14px;
    line-height: 1.35;
  }
  .contact__name {
    color: var(--accent);
    font-weight: 700;
    font-size: 19px;
    margin-bottom: 8px;
  }
  .contact__label { color: var(--accent); font-weight: 700; }
  .contact__site-domain { color: var(--accent); }

  .slogan {
    position: absolute;
    right: 36px;
    bottom: 26px;
    font-weight: 700;
    font-size: 15px;
    color: var(--ink);
  }
</style>
</head>
<body>
  <section class="card card--back" aria-label="Card back">
    <div class="brand">
      <span class="brand__mark"></span>
      <span class="brand__name">hartuvo</span>
    </div>
  </section>

  <section class="card card--front" aria-label="Card front">
    <div class="brand">
      <span class="brand__mark"></span>
      <span class="brand__name">hartuvo</span>
    </div>
    <div class="contact">
      <p class="contact__name">Tobias Lindqvist</p>
      <p><span class="contact__label">P:</span> 0031687203316</p>
      <p><span class="contact__label">E:</span> Tobias@hartuvo.nl</p>
      <p>www.<span class="contact__site-domain">hartuvo</span>.nl</p>
    </div>
    <p class="slogan">Because Quality Matters</p>
  </section>
</body>
</html>
```